Marava Cove Lodge Christmas wishes 2013

We require postcards designed to mail our to our clients for Christmas. We are a SURF travel company, with a high end market and like to mail our Christmas postcards to all our guests that have stayed with us through the year. Front cover will have images and text (ie Seasons Greeting) and our logo. The back will have space for TO: name & address and postage stamp. Will also have some basic text (ie The Management & Staff at Marava Cove Lodge wish you and your family all the best for the Festive Season and New Year. We look forward to seeing you back at Marava Cove Lodge again soon etc etc). Here is link to main image https://www.filecrate-example.com/sh/qwmxrtz481plo/Vb7kRtPwqN

Target Market(s)

Our clients are mostly mature men (40-70) surfers who purchase luxury surf trips

Industry/Entity Type

Travel

Requirements
Must have
• Ocean Image (front)
Logo x 2 in same colour - Orindel & Marava Cove Lodge (front)
Text (front)
Back to be white
Space for name & address (back)
Space for postage stamp (back)
Message (back)
Website www.orindellodges-example.com (back)

```html
<!DOCTYPE html>
<html lang="en">
<head>
<meta charset="UTF-8">
<title>Marava Cove Lodge – Season's Greetings Postcard</title>
<link rel="stylesheet" href="https://fonts.googleapis.com/css2?family=Dancing+Script:wght@700&family=Montserrat:wght@400;500&display=swap">
<style>
  :root {
    --page-bg: #000000;
    --card-white: #f7f7f7;
    --frame-dark: #0b1420;
    --sky-light: #8ab8e6;
    --sky-mid: #3f7cc6;
    --horizon: #1d4f9c;
    --ocean-deep: #164a93;
    --ocean-mid: #1c63ad;
    --ocean-shallow: #2c86bd;
    --ink-white: #ffffff;
    --badge-black: #0a0a0a;
  }
  * { box-sizing: border-box; margin: 0; padding: 0; }
  html, body {
    width: 1200px;
    height: 857px;
    overflow: hidden;
    background: var(--page-bg);
  }
  .postcard {
    position: absolute;
    left: 170px;
    top: 138px;
    width: 860px;
    height: 580px;
    background: var(--card-white);
    padding: 18px;
  }
  .postcard__frame {
    width: 100%;
    height: 100%;
    background: var(--frame-dark);
    padding: 12px;
  }
  .postcard__photo {
    position: relative;
    width: 100%;
    height: 100%;
    background: linear-gradient(to bottom,
      var(--sky-mid) 0%,
      var(--sky-light) 18%,
      #b8d3ee 27%,
      var(--horizon) 30%,
      var(--ocean-deep) 42%,
      var(--ocean-mid) 62%,
      var(--ocean-shallow) 82%,
      var(--ocean-mid) 100%);
    overflow: hidden;
  }
  .postcard__inner-rule {
    position: absolute;
    inset: 12px;
    border: 3px solid var(--ink-white);
    pointer-events: none;
  }
  .greeting {
    position: absolute;
    left: 0;
    right: 0;
    top: 168px;
    text-align: center;
    font-family: "Dancing Script", cursive;
    font-weight: 700;
    font-size: 88px;
    color: var(--ink-white);
    letter-spacing: 1px;
    text-shadow: 0 2px 4px rgba(0, 20, 60, 0.35);
  }
  .lodge-mark {
    position: absolute;
    top: 26px;
    right: 36px;
    text-align: center;
    color: var(--frame-dark);
    font-family: "Montserrat", sans-serif;
  }
  .lodge-mark__dot {
    display: block;
    width: 22px;
    height: 22px;
    margin: 0 auto 4px;
    border-radius: 50%;
    background: var(--frame-dark);
  }
  .lodge-mark__name {
    font-size: 13px;
    font-weight: 500;
    line-height: 1.1;
  }
  .lodge-mark__place {
    font-size: 9px;
    font-weight: 400;
    letter-spacing: 1px;
  }
  .group-badge {
    position: absolute;
    left: 26px;
    bottom: 26px;
    display: flex;
    align-items: center;
    gap: 8px;
    background: var(--badge-black);
    padding: 6px 12px;
    color: var(--ink-white);
    font-family: "Montserrat", sans-serif;
    font-size: 8px;
    font-weight: 500;
    letter-spacing: 1px;
  }
  .group-badge__square {
    width: 12px;
    height: 12px;
    background: var(--ink-white);
  }
</style>
</head>
<body>
  <main class="postcard">
    <div class="postcard__frame">
      <div class="postcard__photo" role="img" aria-label="Ocean photograph: open blue sea under a cloudy sky, a surfer riding a distant wave and a swimmer floating over a clear reef">
        <div class="postcard__inner-rule"></div>
        <div class="lodge-mark">
          <span class="lodge-mark__dot"></span>
          <div class="lodge-mark__name">maravacovelodge-example.com</div>
          <div class="lodge-mark__place">indonesia</div>
        </div>
        <h1 class="greeting">Season’s Greetings</h1>
        <div class="group-badge">
          <span class="group-badge__square"></span>
          <span>ORINDEL LODGES &amp; RESORTS</span>
        </div>
      </div>
    </div>
  </main>
</body>
</html>
```